Cutting Edge Property Services Provider is Looking to Update Business Card Design

We are looking to freshen up our business cards to match our cutting edge technology based image.

KORVANEX - Where Care Finds Its Pulse

More information about our company can be found on our website at www.korvanex-demo.net

We integrate technology in a historically low tech industry.

We have appeared on the Brisk 300/3000 list 2 years in a row and we're previously recognized as the 5th Quickest Rising Firm in San Diego.

Our core colors are blue and white, but are not against accents that might improve our image.

We currently have our Mission Statement on our Business Cards in a folding design:
KORVANEX IS THE LEADING BUILDING SERVICES INNOVATOR. BY COMBINING TECHNOLOGY WITH FUNCTIONAL TOOS THAT IMPROVE EFFICIENCY IN THE WORKPLACE, WE PROVIDE UNPARALLELED SERVICE IN THE INDUSTRY. DEVELOPING LASTING RELATIONSHIPS WITH OUR CLIENTS AND ASSOCIATES IS THE CORNERSTONE OF OUR SUCCESS.

We'd like to convey the image of a cutting edge, technology based company. Want the cards to pop.

Target Market(s)

Commercial Property Managers - 20 to 50 year old professionals

Industry/Entity Type

Business

Requirements
Must have
• Must utilize our logo obviously, but are definitely open to using variations on the logo. Utilizing the components of the logo, but maybe in different configurations or backgrounds, etc...

Must use the Name: KORVANEX.
Can also use KORVANEX PROPERTY SERVICES.

Must include the Mission Statement

Must say: Where Care Finds Its Pulse
Nice to have
• We are considering plastic stock, shaped cards, or folding cards.

Nothing over the top or really expensive, but will consider if it conveys innovation and technology.
Should not have
• No images of toilets, buildings, trees, or anything relating to commercial properties.

We want to convey our technology image.

```html
<!DOCTYPE html>
<html lang="en">
<head>
<meta charset="utf-8">
<title>KORVANEX Business Card</title>
<link rel="stylesheet" href="https://fonts.googleapis.com/css2?family=Rubik:ital,wght@0,300;0,400;0,500;0,700;1,300&display=swap">
<style>
  :root {
    --brand-blue: #0b4a7a;
    --brand-blue-light: #1b6596;
    --accent-orange: #f0592a;
    --paper: #ffffff;
    --ink-grey: #707070;
    --rule-grey: #d2d2d2;
    --canvas-bg: #ecebe8;
    --faint-grey: #f1f1f1;
  }
  * { box-sizing: border-box; margin: 0; padding: 0; }
  html, body { width: 1120px; height: 1200px; overflow: hidden; }
  body {
    background: var(--canvas-bg);
    font-family: "Rubik", Arial, sans-serif;
    position: relative;
  }

  .card {
    position: absolute;
    left: 118px;
    width: 882px;
    height: 502px;
    overflow: hidden;
  }

  /* Front: mission statement */
  .card--mission {
    top: 74px;
    background: var(--brand-blue);
    border-radius: 66px 66px 66px 0;
  }
  .card--mission .wave-decor {
    position: absolute;
    right: -60px;
    bottom: -80px;
    width: 560px;
    height: 420px;
    border-radius: 50%;
    background: radial-gradient(ellipse at 60% 60%, rgba(40,120,170,0.55), rgba(40,120,170,0) 70%);
  }
  .mission-brand {
    position: absolute;
    left: 38px;
    top: 190px;
    width: 253px;
    display: flex;
    align-items: center;
    justify-content: center;
    gap: 12px;
  }
  .mission-brand .brand-mark {
    width: 22px; height: 22px;
    background: var(--paper);
  }
  .mission-brand .brand-name {
    color: var(--paper);
    font-weight: 700;
    font-size: 36px;
    letter-spacing: 1px;
  }
  .mission-divider {
    position: absolute;
    left: 326px;
    top: 128px;
    width: 2px;
    height: 248px;
    background: rgba(255,255,255,0.75);
  }
  .mission-text {
    position: absolute;
    left: 358px;
    top: 122px;
    width: 486px;
    color: var(--paper);
    font-size: 22.5px;
    font-weight: 400;
    line-height: 35px;
    text-align: justify;
  }
  .mission-text .highlight {
    color: var(--accent-orange);
    font-weight: 500;
  }

  /* Back: contact */
  .card--contact {
    top: 624px;
    background: var(--paper);
    border-radius: 66px 66px 0 66px;
  }
  .card--contact .wave-decor {
    position: absolute;
    right: -40px;
    bottom: -120px;
    width: 560px;
    height: 460px;
    border-radius: 50%;
    background: radial-gradient(ellipse at 55% 55%, var(--faint-grey), rgba(241,241,241,0) 70%);
  }
  .person-name {
    position: absolute;
    left: 42px;
    top: 74px;
    color: var(--brand-blue);
    font-weight: 700;
    font-size: 43px;
  }
  .person-role {
    position: absolute;
    left: 42px;
    top: 126px;
    color: var(--ink-grey);
    font-style: italic;
    font-weight: 300;
    font-size: 20px;
  }
  .rule {
    position: absolute;
    left: 36px;
    width: 414px;
    height: 2px;
    background: var(--rule-grey);
  }
  .rule--top { top: 171px; }
  .rule--bottom { top: 347px; }
  .contact-list {
    position: absolute;
    left: 42px;
    top: 190px;
    list-style: none;
  }
  .contact-list li {
    display: flex;
    align-items: center;
    height: 35.5px;
    color: var(--ink-grey);
    font-size: 21px;
    font-weight: 300;
  }
  .contact-list svg { width: 16px; height: 16px; margin-right: 20px; fill: var(--brand-blue); }
  .address {
    position: absolute;
    left: 42px;
    top: 368px;
    display: flex;
    align-items: center;
  }
  .address svg { width: 18px; height: 28px; margin-right: 18px; fill: var(--brand-blue); }
  .address p {
    color: var(--ink-grey);
    font-size: 21px;
    font-weight: 300;
    line-height: 35px;
  }
  .contact-brand {
    position: absolute;
    left: 490px;
    top: 146px;
    width: 350px;
    display: flex;
    align-items: center;
    justify-content: center;
    gap: 14px;
  }
  .contact-brand .brand-mark {
    width: 26px; height: 26px;
    background: var(--brand-blue);
  }
  .contact-brand .brand-name {
    color: var(--brand-blue);
    font-weight: 700;
    font-size: 46px;
    letter-spacing: 1px;
  }
  .tagline {
    position: absolute;
    left: 480px;
    top: 262px;
    width: 370px;
    text-align: center;
    color: var(--ink-grey);
    font-size: 19px;
    font-weight: 400;
    text-transform: uppercase;
  }
</style>
</head>
<body>

<section class="card card--mission">
  <div class="wave-decor" role="img" aria-label="Faint swirl brand decoration"></div>
  <div class="mission-brand">
    <span class="brand-mark"></span>
    <span class="brand-name">KORVANEX</span>
  </div>
  <div class="mission-divider"></div>
  <p class="mission-text"><span class="highlight">KORVANEX</span> is the leading building services innovator. By combining technology with functional tools that improve efficiency in the workplace, we provide unparalleled service in the industry. Developing lasting relationships with our clients and associ-ates is the cornerstone of our succes.</p>
</section>

<section class="card card--contact">
  <div class="wave-decor" role="img" aria-label="Faint swirl brand decoration"></div>
  <h1 class="person-name">Name Surname</h1>
  <p class="person-role">manager</p>
  <div class="rule rule--top"></div>
  <ul class="contact-list">
    <li><svg viewBox="0 0 16 16"><rect x="4" y="1" width="8" height="14" rx="1.5"/><rect x="5.5" y="3" width="5" height="6" fill="#fff"/></svg>+00 123 456 789</li>
    <li><svg viewBox="0 0 16 16"><rect x="4" y="1" width="8" height="4"/><rect x="1" y="6" width="14" height="6" rx="1"/><rect x="4" y="10" width="8" height="5"/></svg>+00 123 456 789</li>
    <li><svg viewBox="0 0 16 16"><rect x="1" y="3" width="14" height="10" rx="1"/><path d="M2 4 L8 9 L14 4" stroke="#fff" stroke-width="1.4" fill="none"/></svg>office@korvanex-demo.net</li>
    <li><svg viewBox="0 0 16 16"><circle cx="8" cy="8" r="6.5" fill="none" stroke="#0b4a7a" stroke-width="1.3"/><ellipse cx="8" cy="8" rx="2.8" ry="6.5" fill="none" stroke="#0b4a7a" stroke-width="1.2"/><path d="M1.5 8 H14.5" stroke="#0b4a7a" stroke-width="1.2"/></svg>www.korvanex-demo.net</li>
  </ul>
  <div class="rule rule--bottom"></div>
  <div class="address">
    <svg viewBox="0 0 18 28"><path d="M9 0 C4 0 0 4 0 9 C0 15 9 28 9 28 C9 28 18 15 18 9 C18 4 14 0 9 0 Z M9 5 A4 4 0 1 1 9 13 A4 4 0 1 1 9 5 Z"/></svg>
    <p>1840 Marlowe Crest Blvd. Suite 220<br>San Diego, CA 92199</p>
  </div>
  <div class="contact-brand">
    <span class="brand-mark"></span>
    <span class="brand-name">KORVANEX</span>
  </div>
  <p class="tagline">Where Care Finds Its Pulse</p>
</section>

</body>
</html>
```